New Business Card Design Project LORVANTI-Italy

we are LORVANTI-Italy
our company in the market for 3 years we are luxury cosmetic company and its about time for a facelift :)
i will like to have elegant luxurious and unique business card
that will give the person that get it a unique, luxurious and elegant impression
I'm VERY OPEN FOR NEW IDEAS , even duo i add a few files of things that i see on line and i like them

i add my logo as well
my website is LORVANTI.COM
(if you would like to see the main style that we have)

Target Market(s)

adult that have money :)

Industry/Entity Type

Business

Contact Information for Business Card

Name - Dario Lorvanti
Position - CEO and CO Founder
address - 4817 E Halvern
telephone - 555-384-1926
email - dario@lorvanti.com
fax - 555-384-1926
website - LORVANTI.COM

Colors
000000
959595
fbee3e
ffffff

Requirements
Must have
• big logo in GOLD color
• elegant look
• impressive
Nice to have
• not must but maybe classy pattern background
• not must but maybe emblem
• maybe clear plastic business card
Should not have
• colors
• images

```html
<!DOCTYPE html>
<html lang="en">
<head>
<meta charset="utf-8">
<title>LORVANTI Italy – Business Card</title>
<link rel="stylesheet" href="https://fonts.googleapis.com/css2?family=Marcellus&family=Open+Sans:wght@400;600&display=swap">
<style>
  :root {
    --backdrop: #3b3431;
    --card-black: #0f1011;
    --card-edge: #1b1c1e;
    --gold: #d9b24c;
    --silver: #cfcfcf;
    --silver-soft: #9a9a9a;
  }
  * { margin: 0; padding: 0; box-sizing: border-box; }
  html, body {
    width: 1200px; height: 864px; overflow: hidden;
    background: var(--backdrop);
  }
  .stage { position: relative; width: 1200px; height: 864px; }

  .card {
    position: absolute;
    width: 540px; height: 308px;
    background: var(--card-black);
    border: 1px solid var(--card-edge);
    border-radius: 4px;
    box-shadow: 0 18px 40px rgba(0,0,0,.45);
  }
  .card--front { left: 50px; top: 150px; }
  .card--back  { left: 610px; top: 406px; }

  /* front */
  .front-brand {
    position: absolute; left: 0; right: 0; top: 52px;
    display: flex; flex-direction: column; align-items: center;
    color: var(--silver);
    font-family: "Marcellus", serif;
  }
  .brand-circle { width: 70px; height: 70px; margin-bottom: 14px; }
  .brand-name { font-size: 46px; letter-spacing: 1px; line-height: 1; }
  .brand-country { font-size: 14px; letter-spacing: 3px; margin-top: 6px; }
  .front-web {
    position: absolute; left: 0; right: 0; bottom: 40px;
    text-align: center;
    font-family: "Open Sans", sans-serif;
    font-size: 15px; letter-spacing: 5px;
    color: var(--silver-soft);
  }

  /* back */
  .contact {
    position: absolute; left: 40px; top: 78px;
    color: var(--gold);
    font-family: "Open Sans", sans-serif;
    font-size: 13px; line-height: 1.5;
  }
  .contact-name { font-family: "Marcellus", serif; font-size: 22px; line-height: 1.1; }
  .contact-role { font-size: 13px; margin-bottom: 16px; }
  .contact-label { font-weight: 600; }

  .back-brand {
    position: absolute; right: 36px; top: 92px; width: 220px;
    display: flex; flex-direction: column; align-items: center;
    color: var(--gold);
    font-family: "Marcellus", serif;
  }
  .back-brand .brand-circle { width: 64px; height: 64px; margin-bottom: 12px; }
  .back-brand .brand-name { font-size: 36px; }
  .back-brand .brand-country { font-size: 12px; }
</style>
</head>
<body>
<main class="stage">

  <section class="card card--front" aria-label="Business card front">
    <div class="front-brand">
      <svg class="brand-circle" viewBox="0 0 70 70" aria-hidden="true">
        <circle cx="35" cy="35" r="32" fill="none" stroke="var(--silver)" stroke-width="2"/>
      </svg>
      <div class="brand-name">LORVANTI</div>
      <div class="brand-country">ITALY</div>
    </div>
    <div class="front-web">www.lorvanti.com</div>
  </section>

  <section class="card card--back" aria-label="Business card back">
    <div class="contact">
      <div class="contact-name">Dario Lorvanti</div>
      <div class="contact-role">CEO &amp; CO Founder</div>
      <div class="contact-line">4817 E Halvern</div>
      <div class="contact-line"><span class="contact-label">PHONE :</span> 555-384-1926</div>
      <div class="contact-line"><span class="contact-label">FAX :</span> 555-384-1926</div>
      <div class="contact-line"><span class="contact-label">EMAIL :</span> dario@lorvanti.com</div>
      <div class="contact-line"><span class="contact-label">WEB :</span> LORVANTI.COM</div>
    </div>
    <div class="back-brand">
      <svg class="brand-circle" viewBox="0 0 64 64" aria-hidden="true">
        <circle cx="32" cy="32" r="29" fill="none" stroke="var(--gold)" stroke-width="2"/>
      </svg>
      <div class="brand-name">LORVANTI</div>
      <div class="brand-country">ITALY</div>
    </div>
  </section>

</main>
</body>
</html>
```